2-Page Flyer for the Information Session about the Quiet Pathfinder Course

This is a flyer to announce/advertise an evening Information Session about the Quiet Pathfinder Course. This Program aims at mindfully rethinking and redesigning work (and life) for people who feel stuck or not entirely satisfied with their work and/or life (please see draft flyer attached for more details). This Program is property of Bright Meadow, a company that uses a combination of Mindfulness, Design, and Entrepreneurship to help people achieve greater happiness (in their work and lives).

Target Market(s)

People who feel stuck or not entirely satisfied with their work and/or life (please see draft flyer attached for more details)

Font styles to use
Serif
Sans Serif

Colors
ffffff
f37122
33a6d7
acd037

Requirements
Must have
• All of what I will say below is suggestive (I’m not a design expert), and I’m open to divert from it, if it makes sense and feels more interesting.
• I thought initially of a 2-page flyer (please see draft flyer attached). The first page could help people grasp the essence of the event quickly (in 1 or 2 minutes), and then, if they are interested/motivated, they would continue reading through page 2, which has more info about the Program in itself.
• Potential Structure
• Page 1
• . About the Information Session on the Quiet Pathfinder Course
• . Visible Date & Time, Contacts, Venue (and other relevant info)
• . About me (the facilitator)
• Page 2
• . About the Quiet Pathfinder Course
• I include a Powerpoint draft of the flyer with the content. The design is rudimentary and precarious from an aesthetics/organization point of view, and this is mainly where I need help (and maybe in other aspects too!).
• On the flyer, I would like to include:
• . A photo of myself (I attach 1 picture).
• . 1 or 2 beautiful-nature photos (cropped or full). One may have to do with looking at the sky, dreaming, and imagining a new work and life (2 photos with sky and clouds attached). The other has to do with walking the transformation journey (the photo with the person walking through the forest path).
• . bright meadow logo or logos (there are two slightly different ones, that can be used for different purposes). For the first page, I would like the bright meadow logo that has "bright meadow" written on the bottom, with the saying "Stillness, Craft and Venture for Bright Meadow" beneath. This is the main logo. For the 2nd page, you can choose the logo that adapts better.
• - Where it says the "the way out is in" it would be great to have a similar font to the one I attach (see file "Font_the_way_out_is_in.png" and Ankecallig-fg.ttf
Nice to have
• In terms of colours, I would not divert much from the logo colours (and of course white and black). I would like the flyer to be quite white. Almost like fairy-tale white: the white horse, the white snow, the white of the stars, the white heaven. White could be the base colour. White means peace, tranquillity, calm contentment, a smile.
• And then use the other colours. The green of the mindfulness. The blue of the sky, the dreams. And the orange of the sun, the energy, the fire, the action. And maybe the black for text.
• Where it says the "the way out is in" it would be great to have a similar font to the one I attach (see file "Font_the_way_out_is_in".
• I would like this flyer to be a piece of art, in every possible way. Simple, beautiful, ease, light, peaceful, calm happy. Just like the Quiet Pathfinder Course and bright meadow Company that I am creating intends to be. The mission of this Program and Company is to be a designer, a painter (a Picasso) of happier and more fulfilling human lives.
• I am very much looking forward to seeing your proposal(s).

```html
<!DOCTYPE html>
<html lang="en">
<head>
<meta charset="utf-8">
<title>Quiet Pathfinder Course – Information Session Flyer</title>
<link href="https://fonts.googleapis.com/css2?family=Arimo:wght@400;700&family=Questrial&family=Archivo+Narrow:wght@400;600&family=Caveat:wght@500&display=swap" rel="stylesheet">
<style>
  :root{
    --white:#ffffff;
    --orange:#f37122;
    --blue:#33a6d7;
    --green:#acd037;
    --ink:#111418;
    --stage:#0e1a24;
    --night:#1b1e28;
    --grey:#9a9ca2;
  }
  *{box-sizing:border-box;margin:0;padding:0}
  html,body{width:1200px;height:670px;overflow:hidden;background:var(--stage)}
  .canvas{position:relative;width:1200px;height:670px}
  .page{position:absolute;top:25px;width:438px;height:620px;overflow:hidden;background:var(--white)}
  .page--front{left:122px;font-family:"Questrial",sans-serif;color:var(--ink)}
  .page--back{left:640px;font-family:"Questrial",sans-serif;color:var(--ink)}

  /* front page */
  .sky-field{position:absolute;inset:0;
    background:linear-gradient(180deg,#3c5fae 0%,#1f3f98 18%,#5f7fc0 30%,#dfe5f1 40%,#f6f7fb 48%,#e6ebf3 56%,#aebfdc 63%,#7e9a6a 69%,#c9ab3f 78%,#e4ad2c 92%,#d99a22 100%)}
  .front-title{position:absolute;left:30px;top:20px;font-family:"Arimo",sans-serif;font-weight:700;font-size:31px;line-height:38px;color:var(--white)}
  .date-box{position:absolute;left:300px;top:40px;width:112px;height:88px;background:rgba(22,22,30,.9);border-radius:0 0 0 12px;color:var(--white);font-size:12.5px;line-height:14px;text-align:center;padding-top:8px}
  .brand{position:absolute;display:flex;align-items:center;gap:7px;font-family:"Questrial",sans-serif;font-size:17px;line-height:17px;color:var(--blue)}
  .brand-dot{width:28px;height:28px;border-radius:50%;background:var(--orange);flex:none}
  .brand--front{left:30px;top:205px}
  .info-session{position:absolute;left:228px;top:190px;width:192px;font-size:9.5px;line-height:11.5px}
  .section-heading{font-size:13px;line-height:15px;margin-bottom:2px}
  .attendance{position:absolute;left:28px;top:262px;width:270px;font-size:9.5px;line-height:11.5px}
  .facilitator-photo{position:absolute;left:30px;top:345px;width:120px;height:160px;background:linear-gradient(160deg,#e9e9e9,#8d8d8d 60%,#4a4a4a)}
  .facilitator-panel{position:absolute;left:150px;top:345px;width:272px;height:185px;background:rgba(10,12,18,.62);color:var(--white);padding:8px 10px;font-size:7.6px;line-height:9.2px}
  .facilitator-name{font-size:9.5px;line-height:11px;margin-bottom:4px}
  .tagline{position:absolute;left:28px;top:548px;font-family:"Arimo",sans-serif;font-weight:700;font-size:9.5px;line-height:11.5px;color:var(--ink)}
  .booking{position:absolute;left:190px;top:540px;width:240px;font-size:8.6px;line-height:10.4px;color:var(--ink)}

  /* back page */
  .intro-band{position:absolute;left:0;top:0;width:438px;height:96px;background:var(--blue);color:var(--white);padding:10px 14px}
  .intro-heading{font-family:"Archivo Narrow",sans-serif;font-weight:600;font-size:15px;line-height:18px;margin-bottom:3px}
  .intro-text{font-size:8.6px;line-height:10.4px}
  .program{position:absolute;left:14px;top:106px;width:178px;font-size:8.2px;line-height:9.8px;color:#555}
  .program-heading{font-family:"Archivo Narrow",sans-serif;font-size:15px;line-height:18px;color:var(--ink);margin-bottom:2px}
  .brand--back{left:290px;top:108px;font-size:17px}
  .cycle{position:absolute;left:200px;top:140px;width:232px;height:110px}
  .cycle text{font-family:"Archivo Narrow",sans-serif}
  .forest{position:absolute;left:0;top:255px;width:438px;height:365px;
    background:linear-gradient(180deg,#4a2f1c 0%,#6b4322 25%,#8a5a2a 45%,#7b7a2c 65%,#93a23a 80%,#5a4a22 100%)}
  .motto{position:absolute;left:0;top:262px;width:438px;text-align:center;font-family:"Caveat",cursive;font-size:30px;color:var(--white)}
  .why-box{position:absolute;left:18px;top:330px;width:200px;height:205px;background:rgba(172,208,55,.78);color:var(--white);padding:7px 9px;font-size:8.3px;line-height:10px}
  .how-box{position:absolute;left:218px;top:352px;width:204px;height:198px;background:rgba(243,113,34,.8);color:var(--white);padding:7px 9px;font-size:8.3px;line-height:10px}
  .box-heading{font-family:"Archivo Narrow",sans-serif;font-size:14px;line-height:17px;margin-bottom:3px}
  .back-contact{position:absolute;left:0;top:570px;width:438px;text-align:center;color:var(--white);font-size:9px;line-height:11px}
</style>
</head>
<body>
<main class="canvas">

  <section class="page page--front">
    <div class="sky-field" role="img" aria-label="Blue sky with white clouds above a golden meadow"></div>
    <h1 class="front-title">Quiet<br>Pathfinder<br>Course</h1>
    <div class="date-box">Thursday 5th<br>September<br>2019<br>19:30 to<br>21:00</div>

    <div class="brand brand--front"><span class="brand-dot"></span><span>bright<br>meadow</span></div>

    <div class="info-session">
      <h2 class="section-heading">Information Session:</h2>
      <p>The purpose of this Information Session is to give you a real insight into the Quiet Pathfinder Course and how it can help you get the most out of your work and life.</p>
    </div>

    <div class="attendance">
      <h2 class="section-heading">How much and who can come?</h2>
      <p>The Information Session is free. Whether you come on your own, or with friends or family, you'll be warmly welcome. It will take place on Thursday the 5th September 2019, from 19:30 to 21:00, at Lantern Coworking. Please get in touch for more info or to book a place.</p>
    </div>

    <div class="facilitator-photo" role="img" aria-label="Black and white portrait of the facilitator"></div>
    <div class="facilitator-panel">
      <p class="facilitator-name">Facilitator: Dr Mateo Lindqvist, Visiting Research Fellow, Westbrook University</p>
      <p>Mateo joined Westbrook University (School of Management) as a Lecturer in Entrepreneurship in 2015. He completed his PhD in Entrepreneurship at Harrowgate Business School in 2014. His work received the Alder Doctoral Thesis Prize from the Guild of Management Scholars. He began his business career as a production engineer (Kestrel Circuits), and continued in sales (Norvale Systems). After his MBA, he worked as a strategy consultant at Riverside School of Business. Originally from Portugal, Mateo enjoys designing and launching new ideas, international communities, mindfulness retreats, and musical improvisation. He nurtures a close connection to Cedar Hollow Mindfulness Centre, where he has practiced and volunteered over 9 months. He has a broad experience of sharing the benefits of mindfulness with others.</p>
    </div>

    <p class="tagline">Stillness, Craft<br>and Venture<br>for Bright Meadow</p>
    <div class="booking">
      <p>Information &amp; Booking:</p>
      <p>Please contact for more information or to book a place</p>
      <p>Email: hello@brightmeadow.example</p>
      <p>Tel: +34 600 000 123 (video call and chat)</p>
      <p>Venue: Lantern Coworking, C/ del Olmo 12, Valmira</p>
    </div>
  </section>

  <section class="page page--back">
    <div class="intro-band">
      <h2 class="intro-heading">What is Quiet Pathfinding</h2>
      <p class="intro-text">Being mindful means being aware and awake. Entrepreneurship is the creation of a new form of organising. The Quiet Pathfinder Course is then the process of creating or redesigning your work and life with awareness, in a way that is reflective of you, of your passions and values, thus conducing to a greater sense of fulfilment and happiness.</p>
    </div>

    <div class="program">
      <h2 class="program-heading">The Program</h2>
      <p>The Quiet Pathfinder Course is a 4-month long transformative journey designed for people who feel stuck or not entirely satisfied with their work and/or life. It is of benefit for everyone, at any stage. The Program consists of a 5-hour workshop each month, with 2-hour weekly peer support meetings. It combines mindfulness techniques, design thinking methodology, and entrepreneurship frameworks.</p>
    </div>

    <div class="brand brand--back"><span class="brand-dot"></span><span>bright<br>meadow</span></div>

    <svg class="cycle" viewBox="0 0 232 110" aria-label="Program cycle of four workshops joined by weekly peer support meetings">
      <defs>
        <marker id="tip" viewBox="0 0 6 6" refX="3" refY="3" markerWidth="4" markerHeight="4" orient="auto"><path d="M0 0L6 3L0 6z" fill="context-stroke"/></marker>
      </defs>
      <path d="M62 32 Q78 20 92 26" stroke="#c9c9c9" stroke-width="3" fill="none" marker-end="url(#tip)"/>
      <path d="M150 30 Q164 32 170 46" stroke="#f2d000" stroke-width="3" fill="none" marker-end="url(#tip)"/>
      <path d="M178 88 Q168 98 152 96" stroke="#33a6d7" stroke-width="3" fill="none" marker-end="url(#tip)"/>
      <path d="M100 90 Q80 92 70 78" stroke="#f37122" stroke-width="3" fill="none" marker-end="url(#tip)"/>
      <circle cx="122" cy="36" r="21" fill="#acd037"/>
      <circle cx="186" cy="66" r="21" fill="#33a6d7"/>
      <circle cx="128" cy="88" r="21" fill="#f37122"/>
      <circle cx="48" cy="58" r="21" fill="#9a9ca2"/>
      <g fill="#fff" font-size="6" text-anchor="middle">
        <text x="122" y="32">Workshop 1</text><text x="122" y="39">INSIGHT</text><text x="122" y="46">(5 hours)</text>
        <text x="186" y="62">Workshop 2</text><text x="186" y="69">DESIGN</text><text x="186" y="76">(5 hours)</text>
        <text x="128" y="84">Workshop 3</text><text x="128" y="91">EXECUTE</text><text x="128" y="98">(5 hours)</text>
        <text x="48" y="54">Workshop 4</text><text x="48" y="61">DESIGN</text><text x="48" y="68">(5 hours)</text>
      </g>
      <g fill="#222" font-size="6.5">
        <text x="20" y="14">WPS meetings</text>
        <text x="160" y="12">Weekly Peer Support</text>
        <text x="166" y="20">WPS meetings</text>
        <text x="172" y="28">(2 hours)</text>
        <text x="0" y="100">WPS meetings</text>
        <text x="182" y="107">WPS meetings</text>
      </g>
    </svg>

    <div class="forest" role="img" aria-label="Person walking along a sunlit forest path between tall trees"></div>
    <p class="motto">“The way out is in”</p>

    <div class="why-box">
      <h2 class="box-heading">Why</h2>
      <p>Many people are not satisfied with their work, but they don't know what to do about it. This Program offers you a safe place to conduct your inner journey with collective support, helping you reflect, design, and (very likely) do something about it. It aims at:</p>
      <p>1) Increasing awareness, clarity and confidence</p>
      <p>2) Having a deeper insight on what makes you happier and what you want</p>
      <p>3) Developing a clear design integrating your intended work and life</p>
      <p>4) Start executing this design.</p>
    </div>

    <div class="how-box">
      <h2 class="box-heading">How</h2>
      <p>This Program differs from existing entrepreneurial programs in many ways:</p>
      <p>1) Uses mindfulness and self analysis to look deeply into yourself</p>
      <p>2) Design and execution decisions are based on happiness rather than (only) financials</p>
      <p>3) Holistic and inclusive design process, integrating work and life, and building synergies between your different parts</p>
      <p>Format includes: lectures, individual work, group sharing, guided activities, experiential exercises, video, audio, handouts and other resources.</p>
    </div>

    <div class="back-contact">
      <p>Email: hello@brightmeadow.example</p>
      <p>Tel: +34 600 000 123 (video call and chat)</p>
    </div>
  </section>

</main>
</body>
</html>
```